Design a cover that embodies the concept of healing by Walking Out of Shadows

Subtitle: How to use tapping, applied kinesiology, and Chinese medicine to heal your body, free your mind and live in peace.

Tapping (Emotional Freedom Technique) is a modern mix of psychology and Chinese medicine that helps people to release the emotions they have inside that are contributing to the depression and anxiety they feel. Applied kinesiology or muscle testing is a biofeedback tool which helps to extract information from the body that can help people to profoundly heal. It can be used to determine whether heavy metals, heavy chemicals, food sensitivities or pathogens are causing the body problems. It can also be used to determine which supplements can help someone heal. This tool also can be used to identify emotions and memories that are also causing someone problems. Lastly, Chinese medicine uses food therapy, herbal formulas, meditation, tai chi (meditative movement), cupping and other tools to help people to be free of depression. This book is written to be information but also details my own personal journey of how I was able to heal from 11 years of heavy depression through the use of these tools.

The heart of the book is about emotional release, emotional freedom and emotional healing. You can surrender, release or let go of emotions and feel better very quickly. This certainly was my experience.

I would like the front and back cover to each be 8.5" x 5.5". I still have to get an ISBN number for the back page as well. Here is the text that I would like on the back cover for now: Millions of people feel the pain, loneliness, and agony of anxiety and depression every day. Many turn to Western medicine in the hopes that a pill will ease the pain and make the problem go away. Oftentimes, this only makes matters worse and doesn’t address the root cause. No one should have to struggle like this when natural answers exist that can address the physical, energetic, emotional, or spiritual causes of anxiety and depression. For 11 long years, Dr. Mervin personally struggled with heavy depression until he discovered answers that helped him to completely heal. Walking Out of Shadows is a guide that will help you discover - The two root physical causes of depression and exactly what to do to start healing today - How the negative emotions we have stored within from trauma and bad experiences can drive depression - Tools from Chinese medicine, applied kinesiology, and tapping to help you free your mind and live in peace - An actionable plan to help you let go of the pain, suffering, and negative emotions from your past Whether you feel depressed and anxious or know someone who struggles with these issues, Walking Out of Shadows will transform how you think about depression and will give you the tools to heal so that you can be free and live in peace. Dr. Mervin Holloway is a board-certified acupuncture physician licensed in the state of Florida. He received his training at the Marlow Institute of Restorative Health. He also graduated with a master’s degree in counseling and psychology from Cedarbrook School of Ministry. His mission is to help people transform their health and improve the quality of their life naturally. He lives in Orlando, FL where he runs a holistic medical clinic called Brightpath Wellness Center. www.drmervinholloway.example Photoline: drmervinholloway Circlenet: brightpathwellnesscenter

Target Market(s)

Those who suffer from depression and anxiety and want to heal naturally

Industry/Entity Type

Health And Wellness

Requirements
Must have
• My picture should be small and go on the back cover next to the information about me. The front cover would be all graphical. Thank you. On the front cover my name should be posted as "Dr. Mervin Holloway, AP, MA"

```html
<!DOCTYPE html>
<html lang="en">
<head>
<meta charset="utf-8">
<title>Walking Out of Shadows – Cover</title>
<link rel="stylesheet" href="https://fonts.googleapis.com/css2?family=Francois+One&family=Abel&family=Cormorant+Garamond:wght@600&family=Gabriela&family=Playfair+Display:wght@700&display=swap">
<style>
  :root {
    --back-bg: #8e9f9f;
    --ink: #111111;
    --body-ink: #1d2222;
    --accent-red: #d0231c;
    --spine-bg: #1c1c1a;
    --spine-ink: #efe6d2;
    --cream: #f4e7c9;
    --white: #ffffff;
  }
  html, body { margin: 0; padding: 0; overflow: hidden; background: #ffffff; }
  .cover {
    position: relative;
    width: 1200px;
    height: 887px;
    overflow: hidden;
  }
  /* Back cover */
  .back {
    position: absolute; left: 0; top: 0;
    width: 576px; height: 887px;
    background: var(--back-bg);
  }
  .back-title {
    position: absolute; left: 64px; top: 54px; width: 456px;
    margin: 0;
    font: 400 47px/1 "Francois One", sans-serif;
    color: var(--ink);
    text-align: center;
    white-space: nowrap;
  }
  .back-title .connector { color: var(--accent-red); font-size: 18px; }
  .blurb {
    position: absolute; left: 64px; top: 116px; width: 456px;
    font: 13.4px/19px "Abel", sans-serif;
    color: var(--body-ink);
    text-align: justify;
  }
  .blurb p { margin: 0 0 19px; }
  .blurb ul { list-style: none; margin: -19px 0 19px; padding: 0; text-align: left; }
  .blurb li { position: relative; padding-left: 7px; }
  .blurb li::before {
    content: ""; position: absolute; left: 0; top: 7px;
    width: 5px; height: 5px; border-radius: 50%;
    background: var(--accent-red);
  }
  .blurb strong { font-weight: 700; color: var(--ink); }
  .author-photo {
    position: absolute; left: 67px; top: 542px;
    width: 153px; height: 150px;
    background: linear-gradient(160deg, #7f9b6a 0%, #b9a98a 55%, #e8dcc2 100%);
  }
  .author-bio {
    position: absolute; left: 240px; top: 538px; width: 280px;
    margin: 0;
    font: 13.4px/19px "Abel", sans-serif;
    color: var(--body-ink);
    text-align: justify;
  }
  .author-bio .name { color: var(--accent-red); font-weight: 700; }
  .contacts {
    position: absolute; left: 64px; top: 766px;
    margin: 0; padding: 0; list-style: none;
    font: 700 14.5px/24px "Playfair Display", serif;
    color: #262626;
  }
  .isbn-space {
    position: absolute; left: 371px; top: 772px;
    width: 147px; height: 91px;
    background: var(--white);
  }
  /* Spine */
  .spine {
    position: absolute; left: 576px; top: 0;
    width: 58px; height: 887px;
    background: var(--spine-bg);
  }
  .spine-title, .spine-author {
    position: absolute; left: 50%;
    transform-origin: 0 0;
    white-space: nowrap;
    color: var(--spine-ink);
  }
  .spine-title {
    top: 62px;
    transform: rotate(90deg) translateY(-50%);
    font: 400 38px/1 "Francois One", sans-serif;
  }
  .spine-title .connector { color: var(--accent-red); font-size: 16px; }
  .spine-author {
    top: 534px;
    transform: rotate(90deg) translateY(-50%);
    font: 600 29px/1 "Cormorant Garamond", serif;
  }
  /* Front cover */
  .front {
    position: absolute; left: 634px; top: 0;
    width: 566px; height: 887px;
  }
  .front-art {
    position: absolute; inset: 0;
    width: 566px; height: 887px;
  }
  .front-author {
    position: absolute; left: 0; top: 8px; width: 566px;
    margin: 0; text-align: center;
    font: 600 33px/1.2 "Cormorant Garamond", serif;
    color: #1a1a1a;
  }
  .front-title {
    position: absolute; left: 0; top: 190px; width: 566px;
    margin: 0; text-align: center;
    color: var(--ink);
    font-family: "Francois One", sans-serif;
    font-weight: 400;
  }
  .front-title .line-1 { display: block; font-size: 66px; line-height: 1.05; }
  .front-title .connector { display: block; font-size: 22px; line-height: 1; color: var(--accent-red); }
  .front-title .line-2 { display: block; font-size: 100px; line-height: 1; }
  .subtitle {
    position: absolute; left: 0; top: 748px; width: 566px;
    margin: 0; text-align: center;
    font: 26px/43px "Gabriela", serif;
    color: var(--cream);
    white-space: nowrap;
  }
</style>
</head>
<body>
<main class="cover">

  <section class="back">
    <h2 class="back-title">Walking Out <span class="connector">of</span> Shadows</h2>
    <div class="blurb">
      <p>Millions of people feel the pain, loneliness, and agony of anxiety and depression every day. Many turn to Western medicine in the hopes that a pill will ease the pain and make the problem go away. Oftentimes, this only makes matters worse and doesn’t address the root cause. No one should have to struggle like this when natural answers exist that can address the physical, energetic, emotional, or spiritual causes of anxiety and depression.</p>
      <p>For 11 long years, <strong>Dr. Mervin</strong> personally struggled with heavy depression until he discovered answers that helped him to completely heal. <strong>Walking Out of Shadows</strong> is a guide that will help you discover:</p>
      <ul>
        <li>The two root physical causes of depression and exactly what to do to start healing today</li>
        <li>How the negative emotions we have stored within from trauma and bad experiences can drive depression</li>
        <li>Tools from Chinese medicine, applied kinesiology, and tapping to help you free your mind and live in peace</li>
        <li>An actionable plan to help you let go of the pain, suffering, and negative emotions from your past.</li>
      </ul>
      <p>Whether you feel depressed and anxious or know someone who struggles with these issues, <strong>Walking Out of Shadows</strong> will transform how you think about depression and will give you the tools to heal so that you can be free and live in peace.</p>
    </div>
    <div class="author-photo" role="img" aria-label="Portrait photograph of the author outdoors"></div>
    <p class="author-bio"><span class="name">Dr. Mervin Holloway</span> is a board-certified acupuncture physician licensed in the state of Florida. He received his training at the Marlow Institute of Restorative Health. He also graduated with a master’s degree in counseling and psychology from Cedarbrook School of Ministry. His mission is to help people transform their health and improve the quality of their life naturally. He lives in Orlando, FL where he runs a holistic medical clinic called Brightpath Wellness Center.</p>
    <ul class="contacts">
      <li>www.drmervinholloway.example</li>
      <li>Photoline: drmervinholloway</li>
      <li>Circlenet: brightpathwellnesscenter</li>
    </ul>
    <div class="isbn-space"></div>
  </section>

  <section class="spine">
    <div class="spine-title">Walking Out <span class="connector">of</span> Shadows</div>
    <div class="spine-author">Dr. Mervin Holloway, AP, MA</div>
  </section>

  <section class="front">
    <svg class="front-art" viewBox="0 0 566 887" role="img" aria-label="Photo collage: a woman in white dancing on a beach by the sea with butterflies, two hands touching at an acupressure point, and a crouched figure dissolving into dust on a wooden deck">
      <defs>
        <linearGradient id="scene" x1="0" y1="0" x2="0" y2="1">
          <stop offset="0" stop-color="#d9dde0"/>
          <stop offset="0.08" stop-color="#aab6bd"/>
          <stop offset="0.2" stop-color="#7d919a"/>
          <stop offset="0.32" stop-color="#c9c8c2"/>
          <stop offset="0.42" stop-color="#d8cfc3"/>
          <stop offset="0.55" stop-color="#b59a82"/>
          <stop offset="0.7" stop-color="#8c6f58"/>
          <stop offset="0.82" stop-color="#5a4a3d"/>
          <stop offset="1" stop-color="#3c332c"/>
        </linearGradient>
      </defs>
      <rect width="566" height="887" fill="url(#scene)"/>
    </svg>
    <p class="front-author">Dr. Mervin Holloway, AP, MA</p>
    <h1 class="front-title">
      <span class="line-1">Walking Out</span>
      <span class="connector">of</span>
      <span class="line-2">Shadows</span>
    </h1>
    <p class="subtitle">How to use tapping, applied kinesiology,<br>and Chinese medicine to heal your body,<br>free your mind and live in peace.</p>
  </section>

</main>
</body>
</html>
```